Modern, clean and professional Wordpress design for a safety training company!

We are currently in the process of creating a new website for our business. We have hired a website developer and the main structure of our new Wordpress site is complete. We now need an overall design plan for the site. We need a very clean, professional and easy to follow website. Most of our website visitors only spend about 30-45 secs on our sites "shopping " so it is imperative that we have a strong Home Page.
Our company specializes in CPR and First Aid Certification Classes to businesses and individuals throughout Northern California. We provide these certifications two ways: ONSITE-We come to you, and HOSTED-we offer weekly classes at our 2 locations.
Our design needs to use the general green and blue colors of our logo. But we also like white.
The final design MUST communicate a legitimate, trustworthy and professional business. Our industry is VERY competitive and we need to STAND OUT.
Currently, the NEW website that we need a new design for is www.LifelineDrillWorks.com
Our old website is www.RescuePrepValleyHub.com and we really do like the design of this website, but we just needed a Wordpress site for SEO purposes.
These are 3 websites that we really:
http://morvaliontech.com/
http://www.tralbex.com/
https://www.plivant.com/
I have attached our Logo and other images if you need to use them but looking at the current two sites will be you best help.
Target Market(s)
1) Large businesses and industries that are looking for a company to provide ONSITE safety training classes at their office or place of work.
2) Individuals that need certifications for their jobs and other needs. These individuals are looking for a legitimate, trustworthy and professional environment to complete their training class.

```html
<!DOCTYPE html>
<html lang="en">
<head>
<meta charset="utf-8">
<title>Lifeline Drill Works – CPR & First Aid Training</title>
<link href="https://fonts.googleapis.com/css2?family=Mulish:wght@400;500;600;700&display=swap" rel="stylesheet">
<style>
:root{
  --green:#8bb510;
  --navy:#0a2484;
  --navy-text:#10288a;
  --ink:#444;
  --rule:#dcdcdc;
  --footer:#2b2b2b;
  --white:#fff;
}
*{box-sizing:border-box;margin:0;padding:0}
html,body{width:900px;height:1200px;overflow:hidden;background:var(--white)}
body{font-family:'Mulish',sans-serif;color:var(--ink);position:relative}
.abs{position:absolute}
.topbar{left:0;top:0;width:900px;height:34px;background:var(--green)}
.social{left:56px;top:6px;display:flex;gap:4px}
.social span{width:22px;height:22px;border-radius:50%;background:var(--white);display:block}
.contact{right:60px;top:10px;color:var(--white);font-size:10.5px;display:flex;align-items:center;gap:8px}
.contact svg{display:block}
.header{left:0;top:34px;width:900px;height:64px}
.brand{left:56px;top:52px;display:flex;align-items:center;gap:6px;color:var(--navy);font-weight:700;font-size:14px;letter-spacing:.3px}
.brand i{width:12px;height:12px;border-radius:50%;background:var(--green);display:block}
.nav{left:263px;top:73px;display:flex;gap:0;font-size:12px;color:#555}
.nav a{color:inherit;text-decoration:none;margin-right:34px}
.nav a.active{color:var(--navy)}
.nav a:last-child{margin-right:0}
.hero{left:0;top:98px;width:900px;height:330px;background:linear-gradient(135deg,#4d4a46 0%,#6f6a63 40%,#3d4355 75%,#5a5650 100%)}
.promo{left:56px;top:315px;width:316px;height:91px;background:rgba(139,181,16,.95);color:var(--white);padding:8px 13px}
.promo h2{font-weight:500;font-size:25px;line-height:1.1}
.promo .price{font-size:11.5px;margin-top:2px}
.promo .price b{color:var(--navy);font-size:24px;font-weight:700;margin-right:2px}
.promo p{font-size:11.5px;color:#1a1a1a;margin-top:-2px}
.promo .btn{position:absolute;left:190px;top:31px;background:var(--navy);color:var(--white);font-size:11.5px;padding:9px 13px;letter-spacing:.3px}
.dots{right:56px;top:397px;display:flex;gap:4px}
.dots span{width:9px;height:9px;border-radius:50%;background:var(--white)}
.dots span:first-child{background:var(--green)}
.welcome{left:56px;top:452px;width:788px;text-align:center}
.welcome h1{color:var(--navy);font-size:19.5px;font-weight:500;margin-bottom:14px}
.welcome p{font-size:10px;line-height:16px;margin-bottom:4px}
.btn-green{background:var(--green);color:var(--white);font-size:10.5px;padding:9px 19px;display:inline-block;letter-spacing:.2px}
.readmore{left:402px;top:584px}
.hrule{left:56px;top:637px;width:789px;height:1px;background:var(--rule)}
.vrule{left:423px;top:670px;width:1px;height:398px;background:var(--rule)}
.offer-title{left:56px;top:666px;color:var(--navy);font-size:19px;font-weight:500}
.offer{left:56px;width:346px}
.offer .photo{height:101px;border:3px solid #ccc}
.offer h3{color:var(--navy);font-size:12.5px;font-weight:500;margin:12px 0 5px}
.offer p{font-size:10px;line-height:14px}
.card{top:670px;width:192px;height:188px;background:var(--navy);color:var(--white);text-align:center;padding:18px 15px 0}
.card h2{font-size:30px;font-weight:500;line-height:1;padding-bottom:10px;border-bottom:1px solid rgba(255,255,255,.2)}
.card div{font-size:11.5px;padding:6px 0;border-bottom:1px solid rgba(255,255,255,.2)}
.card div:last-of-type{border-bottom:none}
.card .btn-green{margin-top:8px;padding:8px 11px}
.rrule{left:450px;top:880px;width:395px;height:1px;background:var(--rule)}
.reviews{left:450px;top:896px;width:395px}
.reviews h2{color:var(--navy);font-size:19px;font-weight:500;margin-bottom:10px}
.reviews h3{color:var(--navy);font-size:11px;font-weight:600;margin-bottom:9px;padding-left:1px}
.reviews p{font-style:italic;font-size:9.5px;line-height:14px;margin-bottom:8px}
.stars{display:flex;gap:1px;margin-bottom:6px}
.reviews .by{font-size:9px}
.reviews .by b{color:var(--navy)}
.reviews .by em{font-style:normal;color:var(--navy)}
.readall{left:749px;top:1039px}
.footer{left:0;top:1093px;width:900px;height:107px;background:var(--footer)}
.fnav{left:56px;top:1117px;font-size:9.5px;color:#ccc}
.fnav span{color:#888;margin:0 7px}
.copy{left:56px;top:1149px;font-size:9px;color:#bbb;line-height:16px}
.copy b{color:var(--green);font-weight:400}
.badge{left:798px;top:1114px;width:42px;height:68px;background:var(--white);border-radius:4px}
</style>
</head>
<body>
<div class="abs topbar"></div>
<div class="abs social" aria-label="Social links"><span></span><span></span><span></span><span></span></div>
<div class="abs contact">
  <svg width="10" height="10" viewBox="0 0 10 10"><rect width="10" height="10" rx="1.5" fill="#fff"/><path d="M3 2.5l1 1.5-.6.6a4 4 0 002 2l.6-.6 1.5 1-.6 1C4.5 8 2 5.5 2 3.1z" fill="#8bb510"/></svg>
  <span>916-555-0172</span><span style="margin:0 3px">|</span>
  <svg width="11" height="8" viewBox="0 0 11 8"><rect width="11" height="8" fill="#fff"/><path d="M0 0l5.5 4.5L11 0" stroke="#8bb510" fill="none"/></svg>
  <span>info@lifelinedrill.com</span>
</div>

<div class="abs header"></div>
<div class="abs brand"><i></i>LIFELINE DRILL WORKS</div>
<nav class="abs nav">
  <a class="active">Home</a><a>Class Calender</a><a>Classes for Groups</a><a>Certification Classes</a><a>About Us</a><a>Policies</a>
</nav>

<div class="abs hero" role="img" aria-label="Photo of responders performing CPR with a defibrillator on a man lying on the ground"></div>
<div class="abs promo">
  <h2>CPR+First Aid</h2>
  <div class="price"><b>$59</b>Adult/Child/Infant</div>
  <p>3 hours or less!</p>
  <span class="btn">REGISTER NOW</span>
</div>
<div class="abs dots"><span></span><span></span><span></span><span></span></div>

<section class="abs welcome">
  <h1>Welcome to Lifeline Drill Works!</h1>
  <p>Lifeline Drill Works is Northern California's leader in CPR, BLS, and Basic First Aid Certifications! Taught by experienced Firefighters, our classes are much shorter and provide common sense knowledge and skills to each student to help prepare them for actual emergencies.</p>
  <p>By using real life emergency responders, we have revolutionized the standard, boring CPR class by teaching students the need-to-know information and preparing them with facts and tips to help them in true life and death situations!</p>
</section>
<span class="abs btn-green readmore">READ MORE</span>
<div class="abs hrule"></div>

<h2 class="abs offer-title">What We Offer</h2>
<div class="abs offer" style="top:700px">
  <div class="photo" role="img" aria-label="Photo of a CPR demonstration on a man lying on grass" style="background:linear-gradient(90deg,#6d7a5a,#8a9a6e 50%,#4c5a3a)"></div>
  <h3>ONSITE-We come to you..</h3>
  <p>Aliquam molestie, mi et imperdiet euismod, dui purus auctor tellus, et interdum lacus lectus et ante. Sed accumsan sollicitudin sapien, sit amet adipiscing turpis gravida ac.</p>
</div>
<div class="abs offer" style="top:898px">
  <div class="photo" role="img" aria-label="Photo of students seated in a classroom" style="background:linear-gradient(180deg,#e4e4e0,#8c7a6a 55%,#5a4a44)"></div>
  <h3>HOSTED-We Offer Weekly Classes..</h3>
  <p>Aliquam molestie, mi et imperdiet euismod, dui purus auctor tellus, et interdum lacus lectus et ante. Sed accumsan sollicitudin sapien, sit amet adipiscing turpis gravida ac.</p>
</div>
<div class="abs vrule"></div>

<div class="abs card" style="left:450px">
  <h2>CPR</h2><div>$39</div><div>Adult/Child/Infant</div><div>90 Minutes!</div>
  <span class="btn-green">REGISTER NOW</span>
</div>
<div class="abs card" style="left:653px">
  <h2>BLS</h2><div>$49</div><div>Healthcare/Dental</div><div>90 Minutes!</div>
  <span class="btn-green">REGISTER NOW</span>
</div>

<div class="abs rrule"></div>
<section class="abs reviews">
  <h2>REVIEWS</h2>
  <h3>It was a very fun CPR class! It was quick...</h3>
  <p>Aliquam molestie, mi et imperdiet euismod, dui purus auctor tellus, et interdum lacus lectus et ante. Sed accumsan sollicitudin sapien, sit amet adipiscing turpis gravida ac.</p>
  <div class="stars">
    <svg width="68" height="13" viewBox="0 0 68 13" fill="#f2c300"><g id="s"><path d="M6.5 0l1.9 4.2 4.6.4-3.5 3 1.1 4.5-4.1-2.4-4.1 2.4 1.1-4.5-3.5-3 4.6-.4z"/></g><use href="#s" x="13.5"/><use href="#s" x="27"/><use href="#s" x="40.5"/><use href="#s" x="54"/></svg>
  </div>
  <div class="by"><b>-Marla T</b>- CA, United States <em>(June 20, 2014)</em></div>
</section>
<span class="abs btn-green readall">READ ALL</span>

<footer class="abs footer"></footer>
<div class="abs fnav">Home<span>/</span>Class Calender<span>/</span>Certification Classes<span>/</span>Classes for Groups<span>/</span>About Us<span>/</span>Policies<span>/</span>Medesto<span>/</span>Manteca/Tracy<span>/</span>Livermore</div>
<div class="abs copy">Copyright © 2015 <b>Lifeline Drill Works</b>.<br>All rights reserved.</div>
<div class="abs badge" role="img" aria-label="Accreditation badge"></div>
</body>
</html>
```